Fernhollow Brochure - A new residential property investment development in Brisbane Queensland *

I need a brochure to entice and inspire customers of financial planners and alike to buy our investment property development, Fernhollow in Greenbank, Australia.

The brochure will be approximately 16 - 18 pages long and will follow a similar format (including maps etc) to the once attached in the uploaded files, however it is important that it has it's own unique style and brand identify. You will have access to all the renders, maps and autocad drawings that will need to be included in the brochure and will be linked in my dropbox link below.

The brochure should feel sophisticated and use the logo we've previously had developed on studio hive. The background and text should also match the style guidelines of our logo's although happy for you to to get creative with the background as long as it is relevant and fits with the colours. For example stock photo's of tree's, people playing, sunlight etc are great - although the context should be in Australia.

There will be a bit of back and forth once I select the winning designer to ensure the brochure is perfect. I'll also need individual files of the masterplan.

Look forward to seeing your designs.

https://www.filecrate-example.net/sh/q8wz3mfa1tp9rdx/KPLx7vnM2_TTqeZb4Hw9kY1uc?dl=0

Target Market(s)

Financial Planners and their consumer customers

Industry/Entity Type

Real Estate Development

Font styles to use
Other font styles liked:
• Monserrat - as per branding guidelines

Requirements
Must have
• At least all the elements that exist in the example brochures and outlined in the content

dropbox link - https://www.filecrate-example.net/sh/q8wz3mfa1tp9rdx/KPLx7vnM2_TTqeZb4Hw9kY1uc?dl=0

```html
<!DOCTYPE html>
<html lang="en">
<head>
<meta charset="utf-8">
<title>Fernhollow Brochure – Introduction Spread</title>
<link href="https://fonts.googleapis.com/css2?family=Montserrat:wght@300;400;500&display=swap" rel="stylesheet">
<style>
  :root {
    --backdrop: #9a9a9a;
    --paper: #f4f4f4;
    --brand-blue: #1d5f86;
    --brand-blue-deep: #174f72;
    --heading-teal: #2c6f93;
    --body-grey: #8a8f94;
    --caption-white: #ffffff;
    --sky: #cfe0ea;
    --render-mid: #b9b6ab;
    --render-ground: #5e6a52;
  }
  * { box-sizing: border-box; margin: 0; padding: 0; }
  html, body {
    width: 1200px;
    height: 900px;
    overflow: hidden;
    background: var(--backdrop);
    font-family: "Montserrat", sans-serif;
  }
  .spread {
    position: absolute;
    left: 50px;
    top: 255px;
    width: 1100px;
    height: 390px;
    display: flex;
  }
  .page {
    position: relative;
    width: 550px;
    height: 390px;
    overflow: hidden;
  }
  .page--left {
    background: linear-gradient(to right, var(--paper) 0 270px, var(--brand-blue) 270px);
  }
  .page--right {
    background: linear-gradient(to right, var(--brand-blue) 0 418px, var(--paper) 418px);
  }
  .intro {
    position: absolute;
    left: 34px;
    top: 112px;
    width: 205px;
  }
  .intro__title {
    font-size: 17px;
    font-weight: 500;
    color: var(--heading-teal);
    letter-spacing: 0.5px;
    margin-bottom: 14px;
  }
  .intro__text {
    font-size: 7.5px;
    line-height: 1.6;
    font-weight: 400;
    color: var(--body-grey);
    margin-bottom: 11px;
  }
  .hero-render {
    position: absolute;
    left: 330px;
    top: 115px;
    width: 754px;
    height: 180px;
    background: linear-gradient(to bottom,
      var(--sky) 0%, #e4ecef 45%, var(--render-mid) 62%, #8d8e80 75%, var(--render-ground) 100%);
  }
  .caption {
    position: absolute;
    right: 148px;
    top: 318px;
    font-size: 12px;
    font-weight: 300;
    letter-spacing: 0.4px;
    color: var(--caption-white);
    white-space: nowrap;
  }
</style>
</head>
<body>
  <main class="spread">
    <section class="page page--left">
      <article class="intro">
        <h1 class="intro__title">Introduction</h1>
        <p class="intro__text">Welcome to Fernhollow Estate, an exclusively crafted neighbourhood, creating better communities to bring people together.</p>
        <p class="intro__text">Fernhollow has been architecturally designed to create an inviting sense of place, with access to superior home design and generous inclusions as standard. Our evolving approach to our design aesthetic enables contemporary comfortable living.</p>
        <p class="intro__text">Nestled between Brisbane and the Gold Coast, Fernhollow is located close to key amenities, services, public transport and major road networks.</p>
        <p class="intro__text">With a limited number of homes available, an investment in Fernhollow provides a unique wealth creation opportunity for the astute investor.</p>
      </article>
    </section>
    <section class="page page--right">
      <p class="caption">an opportunity to invest in long term value creation</p>
    </section>
    <div class="hero-render" role="img" aria-label="Architectural render of a row of single-storey contemporary homes along a tree-lined street"></div>
  </main>
</body>
</html>
```